Webdesign für Personalvermittlung
Zielgruppe
Personalvermittlung
Aufgabenstellung
es soll einladend - nicht zu überladen und natürlich cool und modern sein

```html
<!DOCTYPE html>
<html lang="de">
<head>
<meta charset="utf-8">
<title>pflegeweg job – Angebot</title>
<link href="https://fonts.googleapis.com/css2?family=Raleway:ital,wght@0,400;0,500;0,600;0,700;1,400;1,500&family=Open+Sans:wght@400;600;700&display=swap" rel="stylesheet">
<style>
:root{
  --blue:#29a9e1;
  --orange:#fb8c23;
  --green:#0dbf35;
  --dark:#23202f;
  --ink:#1d1d1d;
  --muted:#8a8f99;
  --field:#3a6fc4;
  --white:#ffffff;
}
*{margin:0;padding:0;box-sizing:border-box}
html,body{width:1200px;height:2483px;overflow:hidden;background:var(--white)}
body{position:relative;font-family:"Raleway",sans-serif;color:var(--ink)}
.abs{position:absolute}

/* header */
.brand{left:82px;top:10px;width:130px;text-align:center}
.brand-dot{width:44px;height:44px;border-radius:50%;background:var(--blue);margin:0 auto 6px}
.brand-name{font-weight:600;font-size:18px;color:#333}
.header-ask{left:650px;top:42px;font-family:"Open Sans",sans-serif;font-size:12px;color:#333}
.header-phone{left:798px;top:40px;font-family:"Open Sans",sans-serif;font-weight:600;font-size:14px;color:var(--blue);display:flex;align-items:center;gap:7px}
.apply-btn{left:966px;top:31px;width:152px;height:38px;border-radius:5px;background:var(--orange);color:var(--white);font-family:"Open Sans",sans-serif;font-weight:600;font-size:17px;display:flex;align-items:center;justify-content:center;gap:8px}

/* nav */
.nav{left:0;top:108px;width:1200px;height:62px;background:var(--blue)}
.nav-item{position:absolute;top:0;height:62px;display:flex;align-items:center;justify-content:center;color:var(--white);font-weight:700;font-size:20px}
.nav-item.active{background:var(--orange)}

/* hero */
.hero{left:51px;top:198px;width:1101px;height:530px;border-radius:16px;overflow:hidden;
  background:linear-gradient(120deg,#6d6e7e 0%,#868797 35%,#9a9aa6 60%,#7a7b8c 100%);
  box-shadow:0 3px 8px rgba(0,0,0,.25)}
.hero-title{left:0;top:82px;width:100%;text-align:center;color:var(--white);font-weight:600;font-size:38px}
.hero-rule{left:214px;top:138px;width:624px;height:2px;background:var(--blue)}
.hero-tag{left:0;top:160px;width:100%;text-align:center;color:var(--white);font-style:italic;font-size:21px;padding-right:40px}
.hero-lead{left:0;top:218px;width:100%;text-align:center;color:var(--white);font-style:italic;font-size:21px;padding-left:20px}

/* form */
.form-title{left:79px;top:796px;color:var(--orange);font-weight:700;font-size:32px}
.form-rule{left:79px;top:846px;width:90px;height:2px;background:var(--blue)}
.form-sub{left:79px;top:854px;font-style:italic;font-size:16px;color:#666}
.label{font-style:italic;font-size:14px;color:var(--ink)}
.field{border:2px solid var(--field);background:var(--white);font-style:italic;font-size:14px;color:var(--muted);padding:0 13px;display:flex;align-items:center}
.field.area{align-items:flex-start;padding-top:14px}
.btn{left:77px;width:963px;height:51px;color:var(--white);font-family:"Open Sans",sans-serif;font-weight:700;font-size:18px;letter-spacing:.5px;display:flex;align-items:center;justify-content:center;border-radius:2px}
.btn-send{top:1532px;background:var(--orange)}
.btn-chat{top:1605px;background:var(--green)}

/* map */
.map{left:8px;top:1716px;width:1192px;height:392px;background:linear-gradient(135deg,#dfe8d8 0%,#e7e9ec 35%,#eceef0 70%,#e3e7e2 100%)}

/* footer */
.footer{left:0;top:2162px;width:1195px;height:212px;background:var(--dark);color:var(--white)}
.footer-brand{left:100px;top:18px;width:212px;text-align:center}
.footer-dot{width:76px;height:76px;border-radius:50%;background:var(--blue);margin:0 auto 10px}
.footer-name{font-weight:600;font-size:28px}
.socials{display:flex;gap:12px;justify-content:center;margin-top:14px}
.socials span{width:23px;height:23px;background:var(--white);display:block}
.footer-head{font-style:italic;font-size:22px;font-weight:400}
.footer-rule{width:70px;height:2px;background:var(--orange);margin-top:14px}
.sitemap{left:431px;top:12px}
.sitemap ul{list-style:none;margin-top:30px;font-style:italic;font-size:14px;line-height:19px}
.sitemap li::before{content:"•";margin-right:9px;font-style:normal}
.subscribe{left:797px;top:12px;width:330px}
.sub-field{margin-top:30px;width:329px;height:49px;background:var(--white);display:flex;align-items:center;padding-left:14px;font-size:15px;color:#8a8a8a}
.sub-field .sep{width:1px;height:22px;background:#ccc;margin:0 14px}
.sub-note{margin-top:16px;font-style:italic;font-size:14px;line-height:19px;color:#e6e6ee}
.copyright{left:0;top:2396px;width:1195px;text-align:center;font-family:"Open Sans",sans-serif;font-size:15px;color:#1f2a6b}
</style>
</head>
<body>

<header>
  <div class="abs brand"><div class="brand-dot"></div><div class="brand-name">pflegeweg job</div></div>
  <div class="abs header-ask">Any QIrgendeine Frage</div>
  <div class="abs header-phone">
    <svg width="16" height="16" viewBox="0 0 24 24" fill="none" stroke="currentColor" stroke-width="2"><path d="M22 16.9v3a2 2 0 0 1-2.2 2 19.8 19.8 0 0 1-8.6-3.1 19.5 19.5 0 0 1-6-6A19.8 19.8 0 0 1 2.1 4.2 2 2 0 0 1 4.1 2h3a2 2 0 0 1 2 1.7c.1 1 .4 1.9.7 2.8a2 2 0 0 1-.5 2.1L8 9.9a16 16 0 0 0 6 6l1.3-1.3a2 2 0 0 1 2.1-.4c.9.3 1.8.6 2.8.7a2 2 0 0 1 1.7 2z"/></svg>
    07000 123 456 7
  </div>
  <div class="abs apply-btn">
    <svg width="16" height="16" viewBox="0 0 24 24" fill="none" stroke="currentColor" stroke-width="2"><path d="M3 21h18M16.5 3.5a2.1 2.1 0 0 1 3 3L7 19l-4 1 1-4z"/></svg>
    ANWENDEN
  </div>
</header>

<nav class="abs nav">
  <div class="nav-item" style="left:104px;width:110px">Home</div>
  <div class="nav-item" style="left:284px;width:160px">Wir Bieten Dir</div>
  <div class="nav-item active" style="left:511px;width:154px">Uber Uns</div>
  <div class="nav-item" style="left:748px;width:110px">Kontakt</div>
</nav>

<section class="abs hero" role="img" aria-label="Foto: Handschlag über einem Schreibtisch mit Klemmbrett in einer Arztpraxis">
  <h1 class="abs hero-title">Angebot</h1>
  <div class="abs hero-rule"></div>
  <p class="abs hero-tag">Ihr Erfolg, unser Engagement</p>
  <p class="abs hero-lead">Bitte füllen Sie das untenstehende Formular aus, um ein Angebot von uns zu erhalten</p>
</section>

<section class="contact-form">
  <h2 class="abs form-title">Nimm ganz einfach Kontakt zu uns auf:</h2>
  <div class="abs form-rule"></div>
  <p class="abs form-sub">gewünschter Rückruf-Zeitpunkt</p>

  <label class="abs label" style="left:85px;top:903px">Vorname</label>
  <div class="abs field" style="left:85px;top:927px;width:438px;height:45px">Gib deinen Namen ein</div>
  <label class="abs label" style="left:593px;top:899px">Nachname</label>
  <div class="abs field" style="left:593px;top:923px;width:439px;height:45px">Gib deinen Namen ein</div>

  <label class="abs label" style="left:85px;top:1001px">E-Mail-Adresse</label>
  <div class="abs field" style="left:85px;top:1026px;width:441px;height:45px">Ihre Emailadresse zur ersten Kontaktaufnahme</div>
  <label class="abs label" style="left:593px;top:1001px">Telefon</label>
  <div class="abs field" style="left:593px;top:1026px;width:439px;height:45px">Sie wünschen telefonischen Kontakt?</div>

  <label class="abs label" style="left:85px;top:1104px">Ich Habe eine Ausbildung als</label>
  <div class="abs field area" style="left:82px;top:1134px;width:951px;height:82px">Ausbildung</div>

  <label class="abs label" style="left:82px;top:1244px">Ich Möchte Arbeiten Els</label>
  <div class="abs field area" style="left:82px;top:1274px;width:953px;height:82px;padding-top:18px">In welchen Bereichen würden Sie gerne arbei</div>

  <label class="abs label" style="left:82px;top:1386px">Das Möchte Ich Auf Keinen Fall</label>
  <div class="abs field area" style="left:82px;top:1415px;width:953px;height:82px;padding-top:18px">Was für Sie nicht in Frage kommt!</div>

  <div class="abs btn btn-send">SENDEN</div>
  <div class="abs btn btn-chat">SENDEN&nbsp; CHATLINK PER FOTO</div>
</section>

<div class="abs map" role="img" aria-label="Karte: Standort von pflegeweg-job.de mit Markierung und umliegenden Straßen"></div>

<footer class="abs footer">
  <div class="abs footer-brand">
    <div class="footer-dot"></div>
    <div class="footer-name">pflegeweg job</div>
    <div class="socials"><span></span><span></span><span></span><span></span></div>
  </div>
  <div class="abs sitemap">
    <div class="footer-head">Seitenverzeichnis</div>
    <div class="footer-rule"></div>
    <ul><li>HOME</li><li>WIR BIETEN DIR</li><li>ÜBER UNS</li><li>KONTAKT</li></ul>
  </div>
  <div class="abs subscribe">
    <div class="footer-head">Abonnieren</div>
    <div class="footer-rule"></div>
    <div class="sub-field">
      <svg width="18" height="14" viewBox="0 0 18 14" fill="none" stroke="#f0a04b" stroke-width="1.5"><rect x="1" y="1" width="16" height="12" rx="3"/><path d="M4 5l5 3 5-3"/></svg>
      <span class="sep"></span>Geben sie ihre E-Mail Adresse ein
    </div>
    <p class="sub-note">Senden Sie eine E-Mail und Sie erhalten regelmäßig unsere Newsletter, Service-Blogs und Pressemitteilungen</p>
  </div>
</footer>

<p class="abs copyright">Copyright 2024 pflegeweg-job.de, All Right Reserved</p>

</body>
</html>
```